Tavenhurst Falcons FC Website

We are looking to develop a new website for Tavenhurst FC. Tavenhurst FC has now joined with Tavenhurst Falcons FC and we are looking at a website that can work for both clubs. Tavenhurst FC play in a local park football competition while tavenhurst Falcons are a Semi Professional team that plays in the Ostral Premier Series Competition. What we are after is two separate website off the one platform. I have attached both team logos for you to visualise. Also you can look at the existing tavenhurst website www.tavenhurstfc.net.au. We are looking for a huge improvement in the website and it will be imperative we have links to sponsors and the sponsors can get regular visuals. Weare looking to move this club forward and have a very professional website that can communicate clearly with the community.

Hi All,

Please remember that the website is to represent two clubs;
1. Tavenhurst Falcons FC (Competes in Semi Professional League)
2. Tavenhurst FC (Compete in KPWLT League which is a lower level)

Further to this the Tavenhurst Falcons FC page will require a player profile page which will show photos of each player and a little bio on each.

Thanks

Reason: Would like to spend more time review existing and new designs

```html
<!DOCTYPE html>
<html lang="en">
<head>
<meta charset="utf-8">
<title>Tavenhurst FC</title>
<link href="https://fonts.googleapis.com/css2?family=Oswald:wght@400;500;700&family=Roboto+Condensed:wght@400;700&family=Crimson+Text:wght@400&display=swap" rel="stylesheet">
<style>
:root{
  --red:#e31e24;
  --red-dark:#c3141a;
  --red-deep:#a80f14;
  --white:#ffffff;
  --ink:#1e1e1e;
  --grey:#f2f2f2;
  --grey-mid:#d9d9d9;
  --grey-text:#3a3a3a;
  --sponsor:#555555;
  --sponsor-shape:#cfcfcf;
  --pitch:#4d6a2c;
}
*{margin:0;padding:0;box-sizing:border-box}
html,body{width:1200px;height:2454px;overflow:hidden;background:var(--white)}
body{position:relative;font-family:"Oswald",sans-serif;color:var(--ink)}
.abs{position:absolute}

/* top bar */
.topbar{left:0;top:0;width:1200px;height:49px;background:var(--red-dark)}
.topbar a{position:absolute;top:0;height:49px;line-height:49px;color:var(--white);font-size:15px;font-weight:500;text-decoration:none;letter-spacing:.5px}
.topbar .sep{position:absolute;top:0;width:1px;height:49px;background:rgba(255,255,255,.35)}
.social{position:absolute;top:14px;display:flex;gap:14px}
.social span{width:20px;height:20px;border-radius:50%;background:var(--white)}

.mainnav{left:0;top:49px;width:1200px;height:103px;background:var(--red)}
.mainnav a{position:absolute;top:0;height:103px;line-height:103px;color:var(--white);font-size:23px;font-weight:500;text-decoration:none}
.mainnav a.active{background:var(--red-deep);padding:0 22px}

.club-mark{left:520px;top:0;width:160px;height:167px;background:var(--white);display:flex;flex-direction:column;align-items:center;justify-content:center;gap:10px;box-shadow:0 2px 6px rgba(0,0,0,.2)}
.club-mark .dot{width:74px;height:74px;border-radius:50%;background:var(--red)}
.club-mark .name{font-size:19px;font-weight:700;color:var(--red)}

/* hero */
.hero{left:0;top:152px;width:1200px;height:761px;background:linear-gradient(180deg,#6f6e63 0%,#4e5946 45%,var(--pitch) 75%,#3d5522 100%)}
.hero-head{right:17px;top:380px;text-align:right;color:var(--white);font-size:52px;font-weight:700;line-height:67px}
.hero-sub{right:17px;top:573px;color:var(--white);font-size:22px;letter-spacing:3px;font-weight:500}
.hero-note{left:780px;top:650px;width:205px;color:var(--white);font-family:"Roboto Condensed",sans-serif;font-size:19px;line-height:24px;font-weight:700}
.hero-thumb{left:994px;top:643px;width:184px;height:123px;border:3px solid var(--white);background:linear-gradient(180deg,#9aa08c,#5d7a3a)}
.see-more{left:989px;top:780px;width:196px;height:32px;background:var(--red);color:var(--white);font-size:18px;font-weight:500;line-height:32px;text-align:center}
.dots{left:1055px;top:877px;display:flex;gap:9px}
.dots span{width:11px;height:11px;border-radius:50%;background:rgba(255,255,255,.6)}
.dots span.on{background:var(--red)}

/* mega menu */
.mega{left:128px;top:152px;width:775px;height:417px;background:var(--red);box-shadow:0 4px 10px rgba(0,0,0,.35)}
.mega .col{position:absolute;top:42px;width:235px}
.mega .col a{display:block;color:var(--white);font-size:17px;font-weight:500;text-decoration:none;height:46px;line-height:46px;border-bottom:1px solid rgba(255,255,255,.35)}
.mega .col a:last-child{border-bottom:none}
.mega .promo{position:absolute;left:0;top:285px;width:775px;height:132px;background:var(--white)}
.promo-art{left:-20px;top:-50px;width:200px;height:170px;background:radial-gradient(circle at 35% 55%,#eeeeee 0 35%,#c93a2f 36% 60%,transparent 61%)}
.promo h3{position:absolute;left:345px;top:20px;font-family:"Crimson Text",serif;font-weight:400;font-size:32px;color:var(--ink)}
.promo .l2{position:absolute;left:345px;top:58px;font-family:"Crimson Text",serif;font-size:19px}
.promo hr{position:absolute;left:345px;top:88px;width:400px;border:none;border-top:1px solid var(--grey-mid)}
.promo .l3{position:absolute;left:345px;top:95px;font-family:"Crimson Text",serif;font-size:16px}
.promo .l3 b{color:var(--red);font-weight:400}

/* club band */
.clubs{left:0;top:913px;width:1200px;height:174px;background:var(--red)}
.clubs .label{position:absolute;left:49px;top:66px;color:var(--white);font-size:36px;font-weight:500;letter-spacing:1px}
.clubs .div{position:absolute;top:0;width:3px;height:174px;background:var(--white)}
.club-pick{position:absolute;top:0;height:174px;color:var(--white)}
.club-pick .stars{position:absolute;top:42px;font-size:22px;letter-spacing:14px}
.club-pick .nm{position:absolute;top:82px;font-size:29px;font-weight:500;line-height:37px;white-space:nowrap}
.club-pick .badge{position:absolute;top:-12px;width:196px;height:196px;border-radius:50%;background:var(--white)}

/* news */
.tag{height:40px;line-height:40px;padding:0 13px;background:var(--red);color:var(--white);font-size:22px;font-weight:500}
.photo{background:linear-gradient(160deg,#3c3530,#7c6a5a 55%,#5a7b3c)}
.news-title{font-size:24px;font-weight:500;line-height:32px}
.para{font-family:"Roboto Condensed",sans-serif;font-weight:700;font-size:18.5px;line-height:24.5px;color:var(--ink)}
.rule{height:1px;background:var(--grey-mid)}

/* sponsors */
.sponsors{left:0;top:1730px;width:1200px;height:417px;background:linear-gradient(180deg,#ffffff,#f4f4f4)}
.ribbon{left:37px;top:1730px;width:1129px;height:61px}
.ribbon-text{left:0;top:1730px;width:1200px;height:56px;line-height:56px;text-align:center;color:var(--white);font-size:34px;font-weight:500;letter-spacing:1px}
.sponsor{display:flex;align-items:center;justify-content:center;gap:12px;width:300px;height:100px}
.sponsor .name{font-family:"Oswald",sans-serif;font-weight:500;font-size:34px;color:var(--sponsor)}
.sponsor .shape{width:34px;height:34px;background:var(--sponsor-shape)}

.redline{left:0;top:2147px;width:1200px;height:5px;background:var(--red)}
.footer{left:0;top:2152px;width:1200px;height:273px;background:linear-gradient(180deg,#e9e9e9,#f7f7f7)}
.fhead{font-size:29px;font-weight:500;color:var(--ink)}
.fline{height:2px;background:var(--grey-mid)}
.flist{font-family:"Roboto Condensed",sans-serif;font-weight:700;font-size:23px;line-height:30px;color:var(--grey-text)}
.bottombar{left:0;top:2425px;width:1200px;height:29px;background:var(--red);color:var(--white);font-family:"Roboto Condensed",sans-serif;font-size:14px;line-height:29px;padding-left:155px}
</style>
</head>
<body>

<header>
  <div class="abs topbar">
    <a style="left:150px">JOIN US NOW ▸</a>
    <span class="sep" style="left:296px"></span>
    <a style="left:332px">GET YOUR TICKETS ▸</a>
    <span class="sep" style="left:500px"></span>
    <span class="sep" style="left:700px"></span>
    <a style="left:732px">FOLLOW US :</a>
    <div class="social" style="left:842px"><span></span><span></span><span></span><span></span><span></span></div>
  </div>
  <nav class="abs mainnav">
    <a style="left:47px">Home</a>
    <a class="active" style="left:130px">Photo Gallery</a>
    <a style="left:322px">Fixture &amp; Results</a>
    <a style="left:704px">News</a>
    <a style="left:800px">Sponsor Club</a>
    <a style="left:968px">Contact Us</a>
    <svg class="abs" style="left:1115px;top:38px" width="28" height="28" viewBox="0 0 28 28"><circle cx="11" cy="11" r="8" fill="none" stroke="#fff" stroke-width="3.5"/><line x1="17" y1="17" x2="25" y2="25" stroke="#fff" stroke-width="4" stroke-linecap="round"/></svg>
  </nav>
  <div class="abs club-mark"><span class="dot"></span><span class="name">TAVENHURST FC</span></div>
</header>

<section>
  <div class="abs hero" role="img" aria-label="Match photo: players in red kit contesting the ball on the pitch"></div>
  <div class="abs hero-head">Tavenhurst FC<br>Premier League1 V 2<br>Marlow Ravens</div>
  <div class="abs hero-sub">Harbour Cup Results</div>
  <div class="abs hero-note">Premier League are knocked out Tavenhurst Falcons FC State league 5 V 1 Brenton</div>
  <div class="abs hero-thumb" role="img" aria-label="Thumbnail of a player on the pitch"></div>
  <div class="abs see-more">SEE MORE ➜</div>
  <div class="abs dots"><span class="on"></span><span></span><span></span><span></span></div>

  <div class="abs mega">
    <div class="col" style="left:30px">
      <a style="font-weight:700">COLLECTIONS</a><a>Birthday Range</a><a>Club Crest Range</a><a>Dressing Room Range</a>
    </div>
    <div class="col" style="left:293px">
      <a>Darren Holt Range</a><a>Harbourbird Range</a><a>TFC Legend Range</a><a>Mighty Red Range</a>
    </div>
    <div class="col" style="left:565px;width:190px">
      <a>Ashworth Range</a><a>Leon Serrano Range</a><a>Simon Garland Range</a><a>Street Sign Range</a>
    </div>
    <div class="promo">
      <div class="abs promo-art" role="img" aria-label="Football and goalkeeper gloves"></div>
      <h3>Spring / Summer</h3>
      <div class="l2">New Colletion online</div>
      <hr>
      <div class="l3">New Tshirts and polos &nbsp;<b>Now available »</b></div>
    </div>
  </div>
</section>

<section class="abs clubs">
  <div class="label">CHOOSE YOUR CLUB:</div>
  <span class="div" style="left:400px"></span>
  <span class="div" style="left:790px"></span>
  <div class="club-pick" style="left:415px;width:370px">
    <div class="stars" style="left:30px">✦✦✦</div>
    <div class="nm" style="left:0">TAVENHURST<br>FALCONS FC</div>
    <div class="badge" style="left:155px"></div>
  </div>
  <div class="club-pick" style="left:805px;width:395px">
    <div class="stars" style="left:30px">✦✦✦</div>
    <div class="nm" style="left:0;top:100px">TAVENHURST FC</div>
    <div class="badge" style="left:185px"></div>
  </div>
</section>

<section>
  <div class="abs tag" style="left:86px;top:1133px">BREAKING NEWS</div>
  <div class="abs photo" style="left:59px;top:1173px;width:527px;height:312px" role="img" aria-label="Striker striking the ball in front of a crowd"></div>
  <div class="abs news-title" style="left:59px;top:1496px">Harbour Cup Results</div>
  <div class="abs rule" style="left:59px;top:1538px;width:527px"></div>
  <p class="abs para" style="left:59px;top:1550px;width:527px">Tavenhurst FC Premier league 1 V 2 Marlow Ravens, Premier League are knocked out Tavenhurst Falcons FC State league 5 V 1 Brenton win and play next week against Marlow Ravens.</p>

  <div class="abs photo" style="left:687px;top:1156px;width:275px;height:169px;background:linear-gradient(180deg,#8b3a34,#5d7d3b 60%,#4a6d2c)" role="img" aria-label="Stadium stands and pitch"></div>
  <div class="abs tag" style="left:706px;top:1134px">RECENT EVENTS</div>
  <div class="abs news-title" style="left:975px;top:1150px">Harbour Cup Results</div>
  <p class="abs para" style="left:975px;top:1186px;width:210px">Tavenhurst FC Premier league 1 V 2 Marlow Ravens, Premier League are knocked out Tavenhurst Falcons FC State league 5 V 1</p>
  <p class="abs para" style="left:687px;top:1335px;width:500px">Brenton win and play next week against Marlow Ravens.</p>

  <div class="abs photo" style="left:687px;top:1438px;width:275px;height:169px;background:linear-gradient(180deg,#3e5a2a,#6b8e3f)" role="img" aria-label="Players celebrating on the pitch"></div>
  <div class="abs tag" style="left:706px;top:1415px">RECENT EVENTS</div>
  <div class="abs news-title" style="left:975px;top:1429px">Harbour Cup Results</div>
  <p class="abs para" style="left:975px;top:1465px;width:210px">Tavenhurst FC Premier league 1 V 2 Marlow Ravens, Premier League are knocked out Tavenhurst Falcons FC State league 5 V 1</p>
  <p class="abs para" style="left:687px;top:1614px;width:500px">Brenton win and play next week against Marlow Ravens.</p>
</section>

<section>
  <div class="abs sponsors"></div>
  <svg class="abs ribbon" viewBox="0 0 1129 61" preserveAspectRatio="none"><polygon points="0,0 1129,0 1110,28 1129,56 0,56 19,28" fill="#e31e24"/><polygon points="30,56 55,56 30,61" fill="#a80f14"/><polygon points="1099,56 1074,56 1099,61" fill="#a80f14"/></svg>
  <div class="abs ribbon-text">✦ OUR GENEROUS SPONSORS ✦</div>

  <div class="abs sponsor" style="left:90px;top:1818px"><span class="name">emberline</span></div>
  <div class="abs sponsor" style="left:450px;top:1818px"><span class="name">brightsmile care</span></div>
  <div class="abs sponsor" style="left:830px;top:1818px"><span class="name">varnell</span></div>
  <div class="abs sponsor" style="left:90px;top:1980px"><span class="name">Protekta</span></div>
  <div class="abs sponsor" style="left:450px;top:1980px"><span class="shape"></span><span class="name">Bylen Finance</span></div>
  <div class="abs sponsor" style="left:830px;top:1980px"><span class="name">NR Ledger Services</span></div>
</section>

<footer>
  <div class="abs redline"></div>
  <div class="abs footer"></div>

  <svg class="abs" style="left:80px;top:2188px" width="56" height="60" viewBox="0 0 56 60"><path d="M12 4h32v16c0 10-7 18-16 18S12 30 12 20z" fill="#f2b705"/><rect x="24" y="38" width="8" height="10" fill="#d99a00"/><rect x="16" y="48" width="24" height="8" fill="#d99a00"/></svg>
  <div class="abs fhead" style="left:150px;top:2200px">HOME</div>
  <div class="abs fline" style="left:150px;top:2252px;width:123px"></div>
  <div class="abs flist" style="left:150px;top:2264px">News<br>Gallery<br>Sponsor<br>Contact Us</div>

  <svg class="abs" style="left:330px;top:2195px" width="56" height="56" viewBox="0 0 56 56"><circle cx="28" cy="28" r="25" fill="#fff" stroke="#222" stroke-width="3"/><circle cx="28" cy="28" r="9" fill="#222"/></svg>
  <div class="abs fhead" style="left:403px;top:2200px">CLUB</div>
  <div class="abs fline" style="left:403px;top:2252px;width:123px"></div>
  <div class="abs flist" style="left:403px;top:2264px">History<br>Committee<br>Awards<br>Forms</div>

  <svg class="abs" style="left:572px;top:2195px" width="70" height="56" viewBox="0 0 70 56"><polygon points="14,6 56,6 68,50 2,50" fill="#5bb53a"/><line x1="35" y1="6" x2="35" y2="50" stroke="#fff" stroke-width="2"/><line x1="8" y1="28" x2="62" y2="28" stroke="#fff" stroke-width="2"/></svg>
  <div class="abs fhead" style="left:660px;top:2200px">FIXTURES &amp; RESULTS</div>
  <div class="abs fline" style="left:660px;top:2252px;width:445px"></div>
  <div class="abs flist" style="left:660px;top:2264px">Premier League<br>Premier League<br>ResSuper League<br>Super League Res</div>
  <div class="abs flist" style="left:960px;top:2264px;width:145px;text-align:right">Under 10 / 2<br>Under 10 / 3<br>Under 11 / 1<br>Under 12 / 3</div>

  <div class="abs bottombar">© 2012-2013 All Rights Reserved to Tavenhurst Falcons FC</div>
</footer>

</body>
</html>
```